Brightfen Business Card Redesign & Logo Update

We need to update our business cards to something more modern and fresh. Brightfen can provide the current color schemes and old design examples, but welcome creativity in helping us with this redesign. PLEASE NOTE that we no longer utilize the "tree" and/or "leaf" imagery in our branding. If able would apprecaite an update on the quality of our "words only" logo in Ai. / PNG formats too.

Target Market(s)

Investors, landowners, corporate partners, contractors

Industry/Entity Type

Environmental Restoration & Conservation

Contact Information for Business Card

Logo, persons name, title, mailing address, phone and email, website url

Font styles to use
Other font styles liked:
• Merriweather

Requirements
Nice to have
• Logo, persons name, title, mailing address, phone and email, website url, but open to ideams
Should not have
• No all back backgrounds

```html
<!DOCTYPE html>
<html lang="en">
<head>
<meta charset="utf-8">
<title>Brightfen Business Card</title>
<link href="https://fonts.googleapis.com/css2?family=Merriweather:wght@400;700;900&display=swap" rel="stylesheet">
<style>
  :root {
    --bg: #e6e7e9;
    --card: #ffffff;
    --orange: #ec7d23;
    --green: #1b7f3e;
    --ink: #2a2a2a;
  }
  * { margin: 0; padding: 0; box-sizing: border-box; }
  html, body { width: 1200px; height: 1059px; overflow: hidden; }
  body {
    background: var(--bg);
    font-family: "Merriweather", Georgia, serif;
    color: var(--ink);
    position: relative;
  }
  .card {
    position: absolute;
    left: 190px;
    width: 820px;
    height: 469px;
    background: var(--card);
    box-shadow: 0 6px 18px rgba(0,0,0,0.18);
    overflow: hidden;
  }
  .card--front { top: 40px; }
  .card--back { top: 550px; }

  .brand { display: flex; flex-direction: column; }
  .brand__name {
    font-weight: 900;
    color: var(--green);
    font-size: 62px;
    letter-spacing: 1px;
    line-height: 1;
    text-transform: uppercase;
  }
  .brand__tagline {
    font-weight: 700;
    font-size: 15px;
    letter-spacing: 1.6px;
    margin-top: 8px;
    text-transform: uppercase;
    color: var(--ink);
  }
  .card--front .brand {
    position: absolute;
    left: 50%; top: 50%;
    transform: translate(-50%, -50%);
    align-items: center;
  }
  .card--back .brand {
    position: absolute;
    left: 54px; top: 190px;
  }
  .card--back .brand__name { font-size: 48px; }
  .card--back .brand__tagline { font-size: 12px; letter-spacing: 1.2px; }

  .swoosh { position: absolute; inset: 0; width: 820px; height: 469px; }

  .contact {
    position: absolute;
    left: 470px; top: 56px;
    padding-left: 24px;
    border-left: 2px solid var(--orange);
    height: 196px;
  }
  .contact__name { font-weight: 900; font-size: 22px; letter-spacing: 0.5px; }
  .contact__first { color: var(--orange); }
  .contact__last { color: var(--green); }
  .contact__title { font-size: 15px; margin-top: 2px; }
  .contact__address { font-size: 15px; margin-top: 16px; line-height: 1.35; }
  .contact__list { list-style: none; margin-top: 14px; font-size: 15px; line-height: 1.45; }
  .contact__list li { display: flex; align-items: center; gap: 8px; }
  .contact__list svg { width: 13px; height: 13px; flex: none; }
</style>
</head>
<body>
  <section class="card card--front">
    <div class="brand">
      <span class="brand__name">Brightfen</span>
      <span class="brand__tagline">Environmental Credit Company</span>
    </div>
  </section>

  <section class="card card--back">
    <svg class="swoosh" viewBox="0 0 820 469" aria-hidden="true">
      <path d="M0 469 L0 452 C300 440 620 360 820 232 L820 469 Z" fill="var(--green)"/>
      <path d="M360 404 C560 350 720 280 820 200 L820 218 C710 296 560 356 360 404 Z" fill="var(--orange)"/>
    </svg>

    <div class="brand">
      <span class="brand__name">Brightfen</span>
      <span class="brand__tagline">Environmental Credit Company</span>
    </div>

    <div class="contact">
      <div class="contact__name"><span class="contact__first">MARCUS</span> <span class="contact__last">HALE</span></div>
      <div class="contact__title">Founder</div>
      <div class="contact__address">Brightfen Company Office<br>14 Marsh Lane, Box 2178</div>
      <ul class="contact__list">
        <li>
          <svg viewBox="0 0 16 16"><path d="M3 1 L6 1 L7 5 L5 6.5 C6 9 7 10 9.5 11 L11 9 L15 10 L15 13 C15 14 14 15 13 15 C6 15 1 10 1 3 C1 2 2 1 3 1 Z" fill="var(--orange)"/></svg>
          (555) 014-2290
        </li>
        <li>
          <svg viewBox="0 0 16 16"><rect x="1" y="3" width="14" height="10" fill="var(--orange)"/><path d="M1 3 L8 9 L15 3" fill="none" stroke="#fff" stroke-width="1.4"/></svg>
          info@brightfenmail.com
        </li>
        <li>
          <svg viewBox="0 0 16 16"><circle cx="8" cy="8" r="7" fill="var(--orange)"/><path d="M1 8 H15 M8 1 C4 5 4 11 8 15 M8 1 C12 5 12 11 8 15" fill="none" stroke="#fff" stroke-width="1"/></svg>
          www.brightfen.com
        </li>
      </ul>
    </div>
  </section>
</body>
</html>
```